Business Card Design

We need a business card designed for our new company. Prefer a black card with white logo & writing.

Contact Information for Business Card

Ted Galloway, address: 7-4812 Fernhollow Road, Abbotsford, BC, V3K 8R2, Office Phone: 604-712-3390, Cell: 604-947-2164, Email: ted@resinworkshub.ca

Colors

Designer to choose only greyscale colors for use in the design.

```html
<!DOCTYPE html>
<html lang="en">
<head>
<meta charset="utf-8">
<title>Resin Works Hub – Business Card</title>
<link href="https://fonts.googleapis.com/css2?family=Poppins:wght@400;700;800&display=swap" rel="stylesheet">
<style>
  :root {
    --backdrop: #2d2d2d;
    --card: #000000;
    --ink: #ffffff;
    --rule: #3a3a3a;
  }
  * { box-sizing: border-box; margin: 0; padding: 0; }
  html, body { width: 1200px; height: 1015px; overflow: hidden; }
  body {
    background: var(--backdrop);
    font-family: "Poppins", sans-serif;
    color: var(--ink);
    display: flex;
    flex-direction: column;
    align-items: center;
    justify-content: center;
    gap: 60px;
  }
  .card {
    width: 700px;
    height: 400px;
    background: var(--card);
    box-shadow: 0 18px 40px rgba(0,0,0,0.45);
    position: relative;
  }
  .brand {
    display: flex;
    align-items: center;
    gap: 14px;
    font-weight: 800;
    letter-spacing: 1px;
    text-transform: uppercase;
    line-height: 1;
  }
  .brand-mark {
    width: 22px;
    height: 22px;
    border: 3px solid var(--ink);
    border-radius: 50%;
    flex: none;
  }
  .card--front {
    display: flex;
    align-items: center;
    justify-content: center;
  }
  .card--front .brand { font-size: 46px; }

  .card--back .brand {
    position: absolute;
    right: 52px;
    top: 92px;
    font-size: 30px;
  }
  .contact {
    position: absolute;
    left: 52px;
    top: 160px;
    width: 320px;
  }
  .contact-name {
    display: flex;
    align-items: center;
    gap: 18px;
    font-weight: 700;
    font-size: 24px;
    letter-spacing: 1px;
    text-transform: uppercase;
  }
  .contact-name::before {
    content: "";
    width: 16px;
    height: 22px;
    background: var(--ink);
  }
  .divider {
    width: 60px;
    height: 1px;
    background: var(--rule);
    margin: 22px 0 22px 36px;
  }
  .contact-list { list-style: none; padding-left: 36px; }
  .contact-list li {
    display: flex;
    align-items: center;
    gap: 10px;
    font-size: 15px;
    line-height: 1.45;
  }
  .contact-list svg { width: 14px; height: 14px; flex: none; }
  .address {
    padding-left: 36px;
    font-size: 15px;
    line-height: 1.45;
    font-style: normal;
  }
</style>
</head>
<body>
  <section class="card card--front">
    <div class="brand"><span class="brand-mark"></span>Resin Works Hub</div>
  </section>

  <section class="card card--back">
    <div class="brand"><span class="brand-mark"></span>Resin Works Hub</div>

    <div class="contact">
      <h1 class="contact-name">Ted Galloway</h1>
      <div class="divider"></div>
      <ul class="contact-list">
        <li>
          <svg viewBox="0 0 24 24" fill="none" stroke="#fff" stroke-width="2.2" aria-hidden="true"><path d="M5 3h4l2 5-2.5 1.5a11 11 0 0 0 6 6L16 13l5 2v4a2 2 0 0 1-2 2A16 16 0 0 1 3 5a2 2 0 0 1 2-2z"/></svg>
          604-712-3390
        </li>
        <li>
          <svg viewBox="0 0 24 24" fill="none" stroke="#fff" stroke-width="2" aria-hidden="true"><rect x="6" y="2" width="12" height="20" rx="2"/><line x1="10" y1="18" x2="14" y2="18"/></svg>
          604-947-2164
        </li>
        <li>
          <svg viewBox="0 0 24 24" fill="none" stroke="#fff" stroke-width="2" aria-hidden="true"><rect x="2" y="5" width="20" height="14"/><path d="M2 5l10 8 10-8"/></svg>
          ted@resinworkshub.ca
        </li>
      </ul>
      <div class="divider"></div>
      <address class="address">
        7-4812 Fernhollow Road,<br>
        Abbotsford, BC, V3K 8R2
      </address>
    </div>
  </section>
</body>
</html>
```